Velmarotix - world unique technology for better life - please let them know who am i at first sight

We need a new business card for company which is a provider of unique crystal based technology suitable for all living being. For more information and final design you can use our brochure (our colours are black and blue from brochure).
We use Verdana font

Industry/Entity Type

Business

Contact Information for Business Card

regular dimension

Font styles to use
Other font styles liked:
• Verdana

Requirements
Must have
• Logo
• name
• function/position
• phone
• mobile
• e-mail
• adress
Nice to have
• inovative design (technology directed)

```html
<!DOCTYPE html>
<html lang="en">
<head>
<meta charset="utf-8">
<title>Velmarotix – Business Card</title>
<link rel="stylesheet" href="https://fonts.googleapis.com/css2?family=Open+Sans:wght@400;600;700&display=swap">
<style>
  :root {
    --bg: #e9e9eb;
    --card-black: #1f1f21;
    --card-black-deep: #161617;
    --brand-blue: #0a9be0;
    --brand-blue-light: #19a9ec;
    --text-light: #d6d6d8;
    --text-muted: #a9a9ad;
    --white: #ffffff;
    --shadow: rgba(0, 0, 0, 0.22);
  }
  * { margin: 0; padding: 0; box-sizing: border-box; }
  html, body {
    width: 1200px; height: 948px; overflow: hidden;
    background: var(--bg);
    font-family: "Open Sans", Verdana, sans-serif;
  }
  .canvas {
    width: 1200px; height: 948px;
    display: flex; flex-direction: column; align-items: center; justify-content: center;
    gap: 56px;
  }
  .card {
    position: relative;
    width: 700px; height: 400px;
    border-radius: 4px;
    overflow: hidden;
    box-shadow: 0 14px 30px var(--shadow);
  }

  /* Front */
  .card--front { background: linear-gradient(160deg, var(--card-black), var(--card-black-deep)); }
  .accent-band {
    position: absolute; left: 0; top: 0; width: 100%; height: 34px;
  }
  .brand {
    position: absolute; left: 58px; top: 62px;
    display: flex; align-items: center; gap: 16px;
  }
  .brand__dot {
    width: 64px; height: 64px; border-radius: 50%;
    background: var(--brand-blue);
  }
  .brand__name {
    font-size: 46px; font-weight: 400; letter-spacing: 2px;
    color: var(--brand-blue);
    text-transform: uppercase;
  }
  .contacts {
    position: absolute; left: 58px; top: 168px;
    list-style: none;
  }
  .contacts__item {
    display: flex; align-items: center; gap: 12px;
    font-size: 15px; color: var(--text-light);
    height: 27px;
  }
  .contacts__icon { width: 16px; height: 16px; flex: none; }
  .contacts__address {
    margin-top: 12px;
    font-size: 15px; color: var(--text-light);
  }
  .person {
    position: absolute; right: 56px; bottom: 52px; text-align: left;
  }
  .person__name {
    font-size: 26px; font-weight: 700; color: var(--brand-blue-light);
  }
  .person__role {
    font-size: 16px; color: var(--text-muted); margin-top: 2px;
  }

  /* Back */
  .card--back {
    background: var(--brand-blue);
    display: flex; flex-direction: column; align-items: center; justify-content: center;
  }
  .back-brand { display: flex; flex-direction: column; align-items: center; gap: 18px; }
  .back-brand__dot {
    width: 132px; height: 132px; border-radius: 50%; background: var(--white);
  }
  .back-brand__name {
    font-size: 28px; font-weight: 400; letter-spacing: 3px; color: var(--white);
    text-transform: uppercase;
  }
  .back-web {
    position: absolute; bottom: 40px; left: 0; width: 100%; text-align: center;
    font-size: 17px; font-weight: 700; letter-spacing: 3px; color: var(--white);
  }
</style>
</head>
<body>
<main class="canvas">

  <section class="card card--front" aria-label="Business card front">
    <svg class="accent-band" viewBox="0 0 700 34" preserveAspectRatio="none" aria-hidden="true">
      <rect x="0" y="0" width="700" height="20" fill="#2c2c2f"/>
      <rect x="0" y="0" width="700" height="6" fill="#0a9be0"/>
      <polygon points="0,0 150,0 120,22 0,22" fill="#0a9be0"/>
    </svg>

    <div class="brand">
      <span class="brand__dot" aria-hidden="true"></span>
      <span class="brand__name">Velmarotix</span>
    </div>

    <ul class="contacts">
      <li class="contacts__item">
        <svg class="contacts__icon" viewBox="0 0 16 16" aria-hidden="true">
          <circle cx="8" cy="8" r="8" fill="#0a9be0"/>
          <path d="M5.2 4.3l1.4-.3.8 1.9-.9.7c.5 1.1 1.3 1.9 2.4 2.4l.7-.9 1.9.8-.3 1.4c-3.2.1-6-2.7-6-6z" fill="#1f1f21"/>
        </svg>
        012-345-6789
      </li>
      <li class="contacts__item">
        <svg class="contacts__icon" viewBox="0 0 16 16" aria-hidden="true">
          <circle cx="8" cy="8" r="8" fill="#0a9be0"/>
          <rect x="5.5" y="3.5" width="5" height="9" rx="1" fill="#1f1f21"/>
          <rect x="6.3" y="4.6" width="3.4" height="5.6" fill="#0a9be0"/>
        </svg>
        012-345-6789
      </li>
      <li class="contacts__item">
        <svg class="contacts__icon" viewBox="0 0 16 16" aria-hidden="true">
          <circle cx="8" cy="8" r="8" fill="#0a9be0"/>
          <rect x="4" y="5" width="8" height="6" fill="#1f1f21"/>
          <path d="M4 5l4 3.2L12 5" stroke="#0a9be0" stroke-width="1" fill="none"/>
        </svg>
        info@velmarotix.com
      </li>
      <li class="contacts__item">
        <svg class="contacts__icon" viewBox="0 0 16 16" aria-hidden="true">
          <circle cx="8" cy="8" r="8" fill="#0a9be0"/>
          <circle cx="8" cy="8" r="4.2" fill="none" stroke="#1f1f21" stroke-width="1.2"/>
          <path d="M3.8 8h8.4M8 3.8c-2 2.5-2 5.9 0 8.4M8 3.8c2 2.5 2 5.9 0 8.4" stroke="#1f1f21" stroke-width="1" fill="none"/>
        </svg>
        www.velmarotix.cu
      </li>
      <li class="contacts__address">Street Name, City Name, Zipcode-01234</li>
    </ul>

    <div class="person">
      <p class="person__name">Mira Kostelac</p>
      <p class="person__role">Founder and CEO</p>
    </div>
  </section>

  <section class="card card--back" aria-label="Business card back">
    <div class="back-brand">
      <span class="back-brand__dot" aria-hidden="true"></span>
      <span class="back-brand__name">Velmarotix</span>
    </div>
    <p class="back-web">www.velmarotix.cu</p>
  </section>

</main>
</body>
</html>
```